Venture 482 - Lumora Book Cover

I am looking for a Lumora book cover for my book about "Venture 482".
The Book is Titled:
Venture 482 Ascended
Shaping Outcomes: Paths To Unlocking Cosmic Truths
Author is Dorian Pell
Here is a book description that may help you understand more about it:
Inspired by the genius of Edwin Marlowe, this comprehensive guide delves into the ancient wisdom and cutting-edge science behind the 482 method, a powerful tool for manifesting your desires. Whether you're seeking personal growth, financial success, or spiritual enlightenment, this book provides advanced techniques and methods to transform your dreams into reality.
Any questions please ask.
Thanks
Owen

```html
<!DOCTYPE html>
<html lang="en">
<head>
<meta charset="utf-8">
<title>Venture 482 Ascended — Dorian Pell</title>
<link rel="stylesheet" href="https://fonts.googleapis.com/css2?family=Cinzel:wght@400;500&family=EB+Garamond:wght@400&display=swap">
<style>
  :root {
    --space-deep: #07061a;
    --space-violet: #2a1446;
    --glow-blue: #3f9bd8;
    --glow-cyan: #7fd6f0;
    --band-red: #d2452c;
    --band-amber: #e88a2c;
    --band-magenta: #a02f8a;
    --author-pink: #f2d5c9;
    --title-cream: #fbeee2;
    --subtitle-white: #ffffff;
  }
  * { margin: 0; padding: 0; box-sizing: border-box; }
  html, body {
    width: 805px;
    height: 1200px;
    overflow: hidden;
    background: var(--space-deep);
  }
  .cover {
    position: relative;
    width: 805px;
    height: 1200px;
    overflow: hidden;
    background: var(--space-deep);
  }
  .cover-art {
    position: absolute;
    inset: 0;
    background:
      radial-gradient(ellipse 32% 40% at 50% 42%, rgba(127,214,240,0.55), rgba(63,155,216,0.25) 55%, transparent 80%),
      linear-gradient(180deg, transparent 44%, rgba(232,138,44,0.35) 50%, rgba(210,69,44,0.35) 55%, rgba(160,47,138,0.35) 63%, transparent 75%),
      radial-gradient(ellipse 90% 80% at 50% 45%, var(--space-violet), var(--space-deep) 85%);
  }
  .author {
    position: absolute;
    top: 70px;
    left: 0;
    width: 100%;
    text-align: center;
    font-family: "Cinzel", serif;
    font-weight: 400;
    font-size: 52px;
    letter-spacing: 0.28em;
    padding-left: 0.28em;
    color: var(--author-pink);
  }
  .title {
    position: absolute;
    top: 548px;
    left: 0;
    width: 100%;
    text-align: center;
    color: var(--title-cream);
    font-family: "Cinzel", serif;
    text-shadow: 0 2px 6px rgba(0,0,0,0.45);
  }
  .title-word {
    display: block;
    font-size: 100px;
    font-weight: 400;
    line-height: 1;
    letter-spacing: 0.01em;
  }
  .title-number {
    display: block;
    font-size: 270px;
    font-weight: 400;
    line-height: 0.9;
    margin-top: -6px;
    letter-spacing: -0.04em;
  }
  .title-tag {
    display: block;
    font-size: 62px;
    font-weight: 400;
    line-height: 1;
    letter-spacing: 0.32em;
    padding-left: 0.32em;
    margin-top: 8px;
  }
  .subtitle {
    position: absolute;
    top: 1030px;
    left: 0;
    width: 100%;
    text-align: center;
    color: var(--subtitle-white);
    font-family: "EB Garamond", serif;
  }
  .subtitle-lead {
    display: block;
    font-size: 30px;
    text-transform: uppercase;
    letter-spacing: 0.01em;
    line-height: 1.2;
    margin-bottom: 12px;
  }
  .subtitle-body {
    display: block;
    font-size: 28px;
    line-height: 1.3;
  }
</style>
</head>
<body>
  <main class="cover">
    <div class="cover-art" role="img" aria-label="Cosmic illustration of a glowing human figure with a column of rainbow chakra points, set against a starry nebula with a bright blue glow and a horizontal band of red, amber and magenta light"></div>

    <p class="author">DORIAN PELL</p>

    <h1 class="title">
      <span class="title-word">VENTURE</span>
      <span class="title-number">482</span>
      <span class="title-tag">ASCENDED</span>
    </h1>

    <p class="subtitle">
      <span class="subtitle-lead">Shaping Outcomes:</span>
      <span class="subtitle-body">Paths to unlocking<br>cosmic truths</span>
    </p>
  </main>
</body>
</html>
```